business card deign

Logo needs the following on it.
1. attached logo
2. Tagline - "From ice-cold coolers to all-night speakers...we bring it!"
3. Name- Dalton Pikes, Founder and CPO
4. Address - 412 E. Carver Avenue, Ste 2207, Tampa, FL. 33917
5. Phone - 555.318.4726

```html
<!DOCTYPE html>
<html lang="en">
<head>
<meta charset="utf-8">
<title>Bilbey Business Card</title>
<link href="https://fonts.googleapis.com/css2?family=Montserrat:wght@400;500;700&display=swap" rel="stylesheet">
<style>
  :root {
    --backdrop: #a8a4a4;
    --ink: #0d0d0d;
    --paper: #ffffff;
    --rule: #333333;
  }
  * { box-sizing: border-box; margin: 0; padding: 0; }
  html, body { width: 1200px; height: 900px; overflow: hidden; }
  body {
    background: var(--backdrop);
    font-family: "Montserrat", sans-serif;
    position: relative;
  }
  .card {
    position: absolute;
    width: 560px;
    height: 320px;
    border-radius: 22px;
    overflow: hidden;
    box-shadow: 0 6px 18px rgba(0,0,0,0.25);
  }
  .card--front {
    left: 80px; top: 110px;
    background: linear-gradient(135deg, #1c1c1c 0%, #050505 60%, #000 100%);
    color: var(--paper);
  }
  .card--back {
    left: 560px; top: 470px;
    background: var(--paper);
    color: var(--ink);
  }
  .brand {
    display: flex;
    align-items: center;
    gap: 12px;
    font-weight: 700;
    letter-spacing: 0.35em;
    white-space: nowrap;
  }
  .brand__dot {
    width: 14px; height: 14px; border-radius: 50%;
    background: currentColor;
    flex: none;
  }
  .card--front .brand {
    position: absolute;
    left: 0; right: 0; top: 118px;
    justify-content: center;
    font-size: 34px;
  }
  .tagline {
    position: absolute;
    left: 0; right: 0; top: 232px;
    text-align: center;
    font-size: 13px;
    font-weight: 400;
    letter-spacing: 0.02em;
  }
  .card--back .brand {
    position: absolute;
    left: 44px; top: 110px;
    font-size: 26px;
  }
  .divider {
    position: absolute;
    left: 262px; top: 34px;
    width: 1px; height: 170px;
    background: var(--rule);
  }
  .person {
    position: absolute;
    left: 290px; top: 34px;
  }
  .person__name { font-size: 22px; font-weight: 700; }
  .person__role { font-size: 13px; font-weight: 400; margin-top: 2px; }
  .contacts {
    position: absolute;
    left: 290px; top: 130px;
    list-style: none;
    font-size: 13px;
  }
  .contacts li {
    display: flex; align-items: center; gap: 10px;
    height: 24px;
  }
  .contacts svg { width: 12px; height: 12px; flex: none; }
  .icon-solid { fill: var(--ink); }
  .icon-line { fill: none; stroke: var(--ink); stroke-width: 2.4; }
  .address-band {
    position: absolute;
    left: 0; right: 0; top: 236px;
    height: 44px;
    background: var(--ink);
    color: var(--paper);
    display: flex; align-items: center; justify-content: center;
    font-size: 13px;
    letter-spacing: 0.02em;
  }
</style>
</head>
<body>

  <section class="card card--front">
    <div class="brand"><span class="brand__dot"></span>BILBEY</div>
    <p class="tagline">From ice-cold coolers to all-night speakers...we bring it</p>
  </section>

  <section class="card card--back">
    <div class="brand"><span class="brand__dot"></span>BILBEY</div>
    <div class="divider"></div>
    <div class="person">
      <h1 class="person__name">Dalton Pikes</h1>
      <p class="person__role">Founder and CPO</p>
    </div>
    <ul class="contacts">
      <li>
        <svg class="icon-solid" viewBox="0 0 24 24" aria-hidden="true"><path d="M6.6 10.8c1.4 2.8 3.8 5.1 6.6 6.6l2.2-2.2c.3-.3.7-.4 1-.2 1.1.4 2.3.6 3.6.6.6 0 1 .4 1 1V20c0 .6-.4 1-1 1C10.6 21 3 13.4 3 4c0-.6.4-1 1-1h3.5c.6 0 1 .4 1 1 0 1.3.2 2.5.6 3.6.1.3 0 .7-.2 1L6.6 10.8z"/></svg>
        555.318.4726
      </li>
      <li>
        <svg class="icon-line" viewBox="0 0 24 24" aria-hidden="true"><rect x="2" y="5" width="20" height="14"/><path d="M2 5l10 8 10-8"/></svg>
        info@bilbey.com
      </li>
      <li>
        <svg class="icon-line" viewBox="0 0 24 24" aria-hidden="true"><circle cx="12" cy="12" r="10"/><path d="M2 12h20M12 2c3 3 3 17 0 20M12 2c-3 3-3 17 0 20"/></svg>
        www.bilbey.com
      </li>
    </ul>
    <div class="address-band">412 E. Carver Avenue, Ste 2207, Tampa, FL. 33917</div>
  </section>

</body>
</html>
```